Thornvale Group needs a business card design

We need a new business card design using the logo recently selected in a logo competition on Pixel Bazaar. Our business is a consultancy specializing in aviation and energy and the winning business card design will promote an image of precision and professionalism with creativity.

Please use the logo with the name on the front of the card and use a complementary font. Make the back white with either the light grey or dark grey logo.

Target Market(s)

Senior finance and legal leaders at aviation and energy companies

Industry/Entity Type

Management Consulting

Contact Information for Business Card

Peter Castrell
President
Thornvale Group

www.thornvalegroup.example

(555) 204-6391
pc@thornvalegroup.example

Requirements
Must have
• Professional font that goes well with the logo font

```html
<!DOCTYPE html>
<html lang="en">
<head>
<meta charset="utf-8">
<title>Thornvale Group — Business Card</title>
<link href="https://fonts.googleapis.com/css2?family=Open+Sans:wght@400;600;700&display=swap" rel="stylesheet">
<style>
  :root {
    --navy: #0f3f75;
    --slate: #636466;
    --mist: #f1f1f1;
    --paper: #ffffff;
    --backdrop: #e4e5e6;
  }
  * { margin: 0; padding: 0; box-sizing: border-box; }
  html, body {
    width: 1200px; height: 900px; overflow: hidden;
    background: var(--backdrop);
    font-family: "Open Sans", Arial, sans-serif;
  }
  .sheet {
    position: relative; width: 1200px; height: 900px;
  }
  .card {
    position: absolute; left: 320px;
    width: 560px; height: 320px;
    background: var(--paper);
    box-shadow: 0 2px 10px rgba(0,0,0,0.12);
    overflow: hidden;
  }
  .card--back { top: 90px; }
  .card--front { top: 490px; }

  /* shared stripe pair */
  .stripe-grey, .stripe-navy { position: absolute; left: 0; right: 0; }
  .stripe-grey { background: var(--slate); height: 7px; }
  .stripe-navy { background: var(--navy); height: 28px; }

  /* back side */
  .card--back .brand-name {
    position: absolute; top: 92px; left: 0; right: 0;
    text-align: center;
    font-size: 40px; font-weight: 400; letter-spacing: 6px;
    color: var(--slate); text-transform: uppercase;
    display: flex; justify-content: center; align-items: center; gap: 16px;
  }
  .brand-square { width: 18px; height: 18px; background: currentColor; display: inline-block; }
  .card--back .tagline {
    position: absolute; top: 172px; left: 0; right: 0; text-align: center;
    font-size: 17px; font-weight: 700; color: var(--navy); letter-spacing: 0.5px;
  }
  .card--back .sectors {
    position: absolute; top: 200px; left: 0; right: 0; text-align: center;
    font-size: 11.5px; font-weight: 400; color: var(--slate); letter-spacing: 1.8px;
  }
  .sectors .dot {
    display: inline-block; width: 6px; height: 6px; border-radius: 50%;
    background: var(--navy); margin: 0 6px; vertical-align: middle;
  }
  .card--back .stripe-grey { top: 240px; }
  .card--back .stripe-navy { top: 247px; }

  /* front side */
  .card--front .person {
    position: absolute; top: 22px; left: 0; right: 0; text-align: center;
  }
  .person-name {
    font-size: 19px; font-weight: 700; color: var(--navy); letter-spacing: 0.5px;
    text-transform: uppercase; line-height: 1.1;
  }
  .person-title { font-size: 11px; color: #222; line-height: 1.3; }
  .card--front .brand-name {
    position: absolute; top: 112px; left: 0; right: 0;
    text-align: center;
    font-size: 28px; font-weight: 400; letter-spacing: 5px;
    color: var(--navy); text-transform: uppercase;
    display: flex; justify-content: center; align-items: center; gap: 12px;
  }
  .card--front .brand-square { width: 13px; height: 13px; }
  .contact-panel {
    position: absolute; top: 178px; left: 0; right: 0; height: 92px;
    background: var(--mist);
  }
  .contact-list {
    position: absolute; top: 198px; left: 0; right: 0;
    list-style: none; text-align: center;
    font-size: 14px; color: #111; line-height: 26px;
  }
  .contact-list li { display: flex; justify-content: center; align-items: center; gap: 6px; }
  .contact-list svg { width: 12px; height: 12px; fill: var(--navy); }
  .card--front .stripe-grey { top: 270px; }
  .card--front .stripe-navy { top: 277px; }
</style>
</head>
<body>
  <main class="sheet">
    <section class="card card--back" aria-label="Card back">
      <div class="brand-name"><span class="brand-square"></span>Thornvale Group</div>
      <p class="tagline">FINANCE AND STRATEGY CONSULTING</p>
      <p class="sectors">AVIATION<span class="dot"></span>MANUFACTURING<span class="dot"></span>ENERGY</p>
      <div class="stripe-grey"></div>
      <div class="stripe-navy"></div>
    </section>

    <section class="card card--front" aria-label="Card front">
      <div class="person">
        <p class="person-name">Peter Castrell</p>
        <p class="person-title">President</p>
      </div>
      <div class="brand-name"><span class="brand-square"></span>Thornvale Group</div>
      <div class="contact-panel"></div>
      <ul class="contact-list">
        <li>
          <svg viewBox="0 0 24 24" aria-hidden="true"><path d="M6.6 10.8a15.1 15.1 0 0 0 6.6 6.6l2.2-2.2a1 1 0 0 1 1-.25 11.4 11.4 0 0 0 3.6.57 1 1 0 0 1 1 1V20a1 1 0 0 1-1 1A17 17 0 0 1 3 4a1 1 0 0 1 1-1h3.5a1 1 0 0 1 1 1c0 1.25.2 2.45.57 3.57a1 1 0 0 1-.25 1z"/></svg>
          (555) 204-6391
        </li>
        <li>
          <svg viewBox="0 0 24 24" aria-hidden="true"><path d="M2 5h20v14H2z M3.5 6.5 12 13l8.5-6.5" fill="var(--navy)"/><path d="M3.5 6.5 12 13l8.5-6.5" fill="none" stroke="#fff" stroke-width="1.6"/></svg>
          pc@thornvalegroup.example
        </li>
      </ul>
      <div class="stripe-grey"></div>
      <div class="stripe-navy"></div>
    </section>
  </main>
</body>
</html>
```